Governance Research Alumni Fellows' Association Annual Symposium Poster

We need a poster to advertise for our annual symposium. The poster will be printed on 11X17" paper.

Our organization is the Governance Research Alumni Fellows' Association. Our logo is in the uploaded files.

The title of this year's symposium is "Lakeside Currents - Paths Beyond Borders." The Symposium will take place on March 31, 2017 in HL - 41.

We are accepting papers on the topics of Canada and the world; Indigenous politics in Canada; Canadian national identity; Race, racialization and belonging; Gender and politics in Canada; Queer politics and sexualities; Class and labour politics in Canada; Environmental politics; Canadian government and politics.

There will be a lunch hour roundtable discussion on the topic of "Unweaving the Threads of Civic Inquiry."
Confirmed Speakers include Dr. Rosalind Okafor, Dr. Teresa Valdomero-Cuesta, Dr. Owen Tillard, Dr. Harriet Brisco
This round-table will consider questions of Race, Indigeneity, and Ethnicity in Political Science Research and efforts by the universities to "Decolonize," "Indigenize," and "Reconcile" the academy.
The roundtable will take place in HL-41 from 12:00 - 1:00 pm.
Lunch will be provided.

There will be a keynote panel sponsored by the Northern Institute for Civilian Safeguard Studies on the topic of "Canada’s renewed vision of peacekeeping."
Their logo is in the uploaded files.

For more information and a full schedule or events, visit our website: http://grafaforum.quillpage.example/credits.html

Sponsors should be listed at the bottom of the page: The Faculty of Arts, The Department of Political Science, NICSS

Target Market(s)

University students and staff who may come to the symposium

Industry/Entity Type

Political

Logo Text

GRAFA Governance Research Alumni Fellows' Association

Font styles to use
Sans Serif

Colors
ec1f27
f37122
9bcb3c
ffcf3e

Requirements
Must have
• Coulours/Leaves/etc should match this website:
• http://grafaforum.quillpage.example/credits.html
• Title of Symposium, Date, Room Number
• Sponsor logos at the bottom of the page
• Date/Time for Roundtable
Nice to have
• This list:
• We are accepting papers on the topics of Canada and the world; Indigenous politics in Canada; Canadian national identity; Race, racialization and belonging; Gender and politics in Canada; Queer politics and sexualities; Class and labour politics in Canada; Environmental politics; Canadian government and politics.
• This statement:
• This round-table will consider questions of Race, Indigeneity, and Ethnicity in Political Science Research and efforts by the universities to "Decolonize," "Indigenize," and "Reconcile" the academy.

```html
<!DOCTYPE html>
<html lang="en">
<head>
<meta charset="utf-8">
<title>Lakeside Currents: Paths Beyond Borders — Symposium Poster</title>
<link rel="stylesheet" href="https://fonts.googleapis.com/css2?family=Oswald:wght@300;400&family=Ubuntu:wght@400;500;700&display=swap">
<style>
  :root {
    --red: #ec1f27;
    --orange: #f37122;
    --green: #9bcb3c;
    --yellow: #ffcf3e;
    --header: #434345;
    --column: #232323;
    --paper: #f1e6dd;
    --ink: #1d1d1f;
    --white: #ffffff;
    --uni-green: #2e7d32;
    --assoc-blue: #1f5fa8;
    --navy: #1c2f5c;
  }
  * { box-sizing: border-box; margin: 0; padding: 0; }
  html, body { width: 1200px; height: 1200px; overflow: hidden; background: var(--white); }
  body { position: relative; font-family: "Ubuntu", sans-serif; color: var(--ink); }

  .poster { position: absolute; left: 225px; top: 22px; width: 750px; height: 1157px; background: var(--paper); overflow: hidden; }

  .masthead { position: absolute; left: 0; top: 0; width: 750px; height: 186px; background: var(--header); border-top: 5px solid var(--red); color: var(--white); text-align: center; }
  .masthead__org { position: absolute; top: 16px; left: 0; right: 0; font-size: 25px; font-weight: 400; letter-spacing: 0.2px; }
  .masthead__presents { position: absolute; top: 54px; left: 0; right: 0; font-size: 21px; }
  .masthead__title { position: absolute; top: 80px; left: 0; right: 0; font-size: 49px; font-weight: 500; line-height: 47px; }

  .leaf { position: absolute; border-radius: 46% 54% 40% 60% / 50% 42% 58% 50%; }
  .leaf--red { left: 0; top: 46px; width: 100px; height: 110px; background: var(--red); transform: rotate(-12deg); }
  .leaf--yellow { left: 652px; top: 72px; width: 96px; height: 104px; background: var(--yellow); transform: rotate(14deg); }
  .leaf--green { left: 628px; top: 236px; width: 108px; height: 108px; background: var(--green); }
  .leaf-cluster { position: absolute; left: 30px; top: 672px; width: 216px; height: 230px; border-radius: 30px; background: radial-gradient(circle at 30% 28%, #9b1e24 0 22%, transparent 36%), radial-gradient(circle at 72% 62%, #a89530 0 22%, transparent 36%), radial-gradient(circle at 32% 78%, #5e9a34 0 20%, transparent 34%); }

  .column { position: absolute; left: 0; top: 186px; width: 271px; height: 856px; background: var(--column); }
  .rule-red { position: absolute; left: 271px; height: 6px; width: 479px; background: var(--red); }

  .label { position: absolute; left: 0; width: 312px; height: 58px; background: var(--orange); color: var(--white); font-family: "Oswald", sans-serif; font-size: 26px; line-height: 58px; padding-left: 19px; letter-spacing: -0.3px; }
  .fold { position: absolute; left: 271px; width: 41px; height: 25px; }

  .speakers { position: absolute; left: 17px; top: 455px; color: var(--white); font-family: "Oswald", sans-serif; font-weight: 300; font-size: 14.5px; line-height: 20.5px; }
  .speakers__heading { margin-bottom: 20px; }

  .divider { position: absolute; left: 324px; width: 394px; height: 3px; background: var(--green); }

  .info { position: absolute; left: 335px; font-weight: 500; font-size: 22px; line-height: 25px; }
  .roundtable__title { position: absolute; left: 355px; top: 442px; font-size: 19.5px; font-weight: 500; text-decoration: underline; text-underline-offset: 3px; }
  .roundtable__text { position: absolute; left: 355px; top: 469px; width: 352px; font-size: 15.2px; line-height: 20.3px; text-align: justify; }

  .panel__heading { position: absolute; left: 335px; top: 606px; font-size: 21.5px; font-weight: 500; }
  .topics { position: absolute; left: 342px; top: 634px; list-style: none; font-size: 15.5px; line-height: 24.7px; }
  .topics li::before { content: ""; display: inline-block; width: 8px; height: 8px; border-radius: 50%; background: var(--ink); margin-right: 10px; vertical-align: 2px; }

  .keynote__title { position: absolute; left: 335px; top: 913px; width: 372px; font-size: 22px; font-weight: 500; line-height: 27px; }
  .keynote__sponsor { position: absolute; left: 355px; top: 982px; width: 340px; font-size: 15.5px; line-height: 21px; }

  .footer-band { position: absolute; left: 0; top: 1042px; width: 750px; height: 8px; background: var(--column); }
  .sponsors { position: absolute; left: 0; top: 1050px; width: 750px; height: 107px; display: flex; align-items: center; }
  .sponsor { flex: none; display: flex; align-items: center; justify-content: center; height: 68px; }
  .sponsor + .sponsor { border-left: 2px solid #3a3a3a; }
  .sponsor--uni { width: 275px; gap: 9px; color: var(--uni-green); font-weight: 700; font-size: 13px; line-height: 16px; }
  .sponsor--uni .mark { width: 22px; height: 22px; background: var(--uni-green); }
  .sponsor--assoc { width: 238px; color: var(--assoc-blue); font-weight: 700; font-size: 34px; }
  .sponsor--institute { width: 237px; gap: 8px; color: var(--navy); font-weight: 500; font-size: 36px; }
  .sponsor--institute .mark { width: 16px; height: 16px; border-radius: 50%; background: var(--red); }
</style>
</head>
<body>
<main class="poster">
  <header class="masthead">
    <p class="masthead__org">The Governance Research Alumni Fellows' Association</p>
    <p class="masthead__presents">Presents</p>
    <h1 class="masthead__title">Lakeside Currents:<br>Paths Beyond Borders</h1>
    <div class="leaf leaf--red" role="img" aria-label="Red maple leaf"></div>
    <div class="leaf leaf--yellow" role="img" aria-label="Yellow maple leaf"></div>
  </header>

  <div class="column"></div>
  <div class="rule-red" style="top:184px"></div>
  <div class="rule-red" style="top:1036px"></div>

  <div class="label" style="top:197px">DATE OF SYMPOSIUM</div>
  <div class="label" style="top:281px">ROOM NUMBER</div>
  <div class="label" style="top:364px">LUNCHTIME ROUNDTABLE</div>
  <div class="label" style="top:604px">STUDENT PANEL DISCUSSIONS</div>
  <div class="label" style="top:923px">KEYNOTE PANEL</div>

  <svg class="fold" style="top:255px" viewBox="0 0 41 25"><polygon points="0,10 41,0 0,25" fill="var(--red)"/></svg>
  <svg class="fold" style="top:339px" viewBox="0 0 41 25"><polygon points="0,10 41,0 0,25" fill="var(--red)"/></svg>
  <svg class="fold" style="top:422px" viewBox="0 0 41 25"><polygon points="0,10 41,0 0,25" fill="var(--red)"/></svg>
  <svg class="fold" style="top:662px" viewBox="0 0 41 25"><polygon points="0,10 41,0 0,25" fill="var(--red)"/></svg>
  <svg class="fold" style="top:981px" viewBox="0 0 41 25"><polygon points="0,10 41,0 0,25" fill="var(--red)"/></svg>

  <div class="speakers">
    <p class="speakers__heading">CONFIRMED SPEAKERS:</p>
    <p>DR. ROSALIND OKAFOR</p>
    <p>DR. TERESA VALDOMERO-CUESTA</p>
    <p>DR. OWEN TILLARD</p>
    <p>DR. HARRIET BRISCO</p>
  </div>

  <div class="leaf-cluster" role="img" aria-label="Three autumn maple leaves in red, olive and green"></div>

  <p class="info" style="top:206px">MARCH 31, 2017<br>9AM - 5PM</p>
  <div class="divider" style="top:275px"></div>
  <p class="info" style="top:300px">HL - 41</p>
  <div class="divider" style="top:339px"></div>
  <div class="leaf leaf--green" role="img" aria-label="Green maple leaf"></div>

  <p class="info" style="top:371px">FRIDAY, MARCH 31ST, 2017<br>12:00 - 1:00 PM</p>
  <h2 class="roundtable__title">Unweaving the Threads of Civic Inquiry</h2>
  <p class="roundtable__text">This round-table will consider questions of Race, Indigeneity, and Ethnicity in Political Science Research and efforts by the universities to "Decolonize," "Indigenize," and "Reconcile" the academy.</p>
  <div class="divider" style="top:580px"></div>

  <h2 class="panel__heading">Panel discussion will consider:</h2>
  <ul class="topics">
    <li>Canada and the World</li>
    <li>Indigenous Politics in Canada</li>
    <li>Canadian National Identity</li>
    <li>Race</li>
    <li>Racialization and Belonging</li>
    <li>Gender and Politics in Canada</li>
    <li>Queer Politics and Sexualities</li>
    <li>Class and Labour Politics in Canada</li>
    <li>Environmental politics</li>
    <li>Canadian Government and Politics.</li>
  </ul>
  <div class="divider" style="top:903px"></div>

  <h2 class="keynote__title">Canada's Renewed Vision of Peacekeeping</h2>
  <p class="keynote__sponsor">Sponsored by the Northern Institute for Civilian Safeguard Studies</p>

  <div class="footer-band"></div>
  <footer class="sponsors">
    <div class="sponsor sponsor--uni">
      <span class="mark"></span>
      <span>NORTHGATE UNIVERSITY<br>FACULTY OF ARTS<br>Department of Political Science</span>
    </div>
    <div class="sponsor sponsor--assoc">GRAFA</div>
    <div class="sponsor sponsor--institute">NICSS<span class="mark"></span></div>
  </footer>
</main>
</body>
</html>
```